Facebook post - Kestrel Bay Finishes has arrived to make your tiles smile!

Kestrel Bay Finishes would like to release a Facebook post calling out to the market that we have arrived. The company has a new and fresh branding aiming for a female demographic between the ages of 40 and 55 located in the South West of Western Australia. The company image MUST be centered around trust! Our Primary aim is to create an uncompromising trust from the very first impression. Our logo tag line is, 'We love to make your tiles smile'.
I need 5 x facebook template designs and also 5 x posts.
Our 1st campaign is to be 5 x posts centered around the arrival of this fantastic new company.
We are company that provides the services of:
- Grout and silicone repair.
- Broken or drummy tile replacement and;
- Grout sealing
Dont forget that we must communicate TRUST and the we love to make your tiles SMILE!

```html
<!DOCTYPE html>
<html lang="en">
<head>
<meta charset="utf-8">
<title>Kestrel Bay Finishes – Ad Design</title>
<link href="https://fonts.googleapis.com/css2?family=Bebas+Neue&family=Poppins:wght@600;700;800&family=Montserrat:wght@400;500;600&display=swap" rel="stylesheet">
<style>
  :root {
    --board: #d7dae3;
    --brand-blue: #2b9fd9;
    --brand-blue-deep: #1f8fcc;
    --label-blue: #1f6fbf;
    --ink: #3f3f42;
    --ink-soft: #4a4a4d;
    --white: #ffffff;
    --black: #111111;
  }
  * { margin: 0; padding: 0; box-sizing: border-box; }
  html, body { width: 1200px; height: 805px; overflow: hidden; }
  body { background: var(--board); position: relative; font-family: "Poppins", sans-serif; }

  .side-label {
    position: absolute; left: 35px; top: 310px;
    transform: translate(-50%, -50%) rotate(-90deg);
    font-family: "Montserrat", sans-serif; font-weight: 500;
    font-size: 25px; letter-spacing: 0.5px; color: var(--label-blue); white-space: nowrap;
  }
  .size-label {
    position: absolute; top: 598px; width: 513px; text-align: center;
    font-family: "Montserrat", sans-serif; font-weight: 500;
    font-size: 27px; color: var(--label-blue); letter-spacing: 1px;
  }
  .progress-note {
    position: absolute; left: 0; right: 32px; top: 682px; text-align: center;
    font-family: "Montserrat", sans-serif; font-weight: 500; color: var(--black);
    font-size: 32px; line-height: 38px;
  }

  .post {
    position: absolute; top: 55px; width: 513px; height: 513px;
    background: var(--white); overflow: hidden;
    box-shadow: 0 2px 6px rgba(0,0,0,0.25);
  }
  .post--tiles { left: 70px; }
  .post--smile { left: 617px; }

  .photo-backdrop { position: absolute; left: 0; top: 0; width: 513px; height: 513px; }
  .post--tiles .photo-backdrop {
    height: 303px;
    background: linear-gradient(160deg, #f4f4f3 0%, #e8e7e4 45%, #f1f1ef 100%);
  }
  .post--smile .photo-backdrop {
    background: linear-gradient(100deg, #eef2f4 0%, #e4eef4 40%, #d5e7f1 70%, #eaf3f8 100%);
  }

  .brand-name {
    position: absolute; top: 120px; width: 180px; text-align: center;
    font-family: "Bebas Neue", sans-serif; font-size: 21px; line-height: 1;
    color: var(--brand-blue); white-space: nowrap;
  }
  .brand-mark {
    position: absolute; top: 62px; width: 40px; height: 40px; border-radius: 50%;
    border: 5px solid var(--brand-blue);
  }

  .headline-big {
    position: absolute; left: 36px; top: 150px;
    font-family: "Bebas Neue", sans-serif; font-size: 90px; line-height: 1;
    color: var(--brand-blue);
  }
  .headline-sub {
    position: absolute; left: 29px; top: 264px;
    font-family: "Bebas Neue", sans-serif; font-size: 36px; line-height: 1;
    color: var(--ink);
  }
  .headline-sub .accent { color: var(--brand-blue); }

  .values {
    position: absolute; left: 272px; top: 28px;
    font-family: "Bebas Neue", sans-serif; font-size: 45px; line-height: 39px;
    color: var(--brand-blue);
  }
  .tagline {
    position: absolute; left: 29px; top: 170px;
    font-family: "Bebas Neue", sans-serif; font-size: 38px; line-height: 36px;
    color: var(--ink);
  }
  .tagline .accent { color: var(--brand-blue); }

  .smile-swoosh { position: absolute; left: 0; top: 0; }

  .service-band {
    position: absolute; left: 0; top: 303px; width: 513px; height: 110px;
    background: linear-gradient(180deg, #2a9ed8 0%, #3aa7dc 55%, #9dd3ef 100%);
  }
  .post--smile .service-band {
    background: linear-gradient(180deg, rgba(38,154,214,0.95) 0%, rgba(56,165,220,0.9) 55%, rgba(150,205,235,0.85) 100%);
  }
  .service-list { list-style: none; position: absolute; left: 24px; top: 308px; }
  .service-item {
    display: flex; align-items: center; height: 32px;
    font-weight: 600; font-size: 14px; color: var(--white); white-space: nowrap;
  }
  .service-item svg { width: 28px; height: 28px; margin-right: 10px; flex: none; }

  .photo-slot--smile {
    position: absolute; left: 322px; top: 155px; width: 191px; height: 358px;
    background: linear-gradient(180deg, #7a4f36 0%, #c99a80 30%, #e6c3ad 55%, #f2ebe6 80%, #f7f5f3 100%);
    border-radius: 90px 0 0 0;
  }

  .cta { position: absolute; left: 22px; top: 430px; }
  .cta-title {
    font-weight: 800; font-size: 26.5px; line-height: 30px; color: var(--brand-blue);
    white-space: nowrap;
  }
  .cta-phone {
    font-family: "Montserrat", sans-serif; font-weight: 500;
    font-size: 28px; line-height: 32px; letter-spacing: 3.6px; color: var(--ink-soft);
    white-space: nowrap;
  }

  .contact-pill {
    position: absolute; left: 268px; width: 226px; height: 26px; border-radius: 13px;
    background: var(--brand-blue); display: flex; align-items: center; padding-left: 8px;
    font-family: "Montserrat", sans-serif; font-weight: 500; font-size: 10.2px; color: var(--white);
    white-space: nowrap;
  }
  .contact-pill svg { width: 17px; height: 17px; margin-right: 7px; flex: none; }
  .contact-pill--email { top: 427px; }
  .contact-pill--web { top: 468px; }
</style>
</head>
<body>

<div class="side-label">AD DESIGN</div>

<!-- Post 1: Your tiles matter -->
<section class="post post--tiles">
  <div class="photo-backdrop" role="img" aria-label="Soft background photo of a gloved hand spreading grout across white tiles"></div>

  <div class="brand-mark" style="left:105px"></div>
  <div class="brand-name" style="left:35px">KESTREL BAY FINISHES</div>

  <div class="headline-big">YOUR</div>
  <svg class="smile-swoosh" width="513" height="513" viewBox="0 0 513 513" aria-hidden="true">
    <path d="M22,232 C90,262 170,260 230,232 C170,252 90,254 22,232 Z" fill="none" stroke="#2b9fd9" stroke-width="4" stroke-linecap="round"/>
  </svg>
  <div class="headline-sub">TILES <span class="accent">MATTERS</span></div>

  <div class="service-band"></div>

  <svg width="513" height="513" viewBox="0 0 513 513" style="position:absolute;left:0;top:0" aria-hidden="true">
    <path d="M427,-5 C440,60 540,150 551,271 A130,130 0 1 1 291,271 C298,180 400,90 427,-5 Z" fill="#2b9fd9" stroke="#ffffff" stroke-width="3"/>
  </svg>
  <svg width="513" height="513" viewBox="0 0 513 513" style="position:absolute;left:0;top:0" role="img" aria-label="Portrait photo of a smiling woman with blonde hair">
    <defs>
      <linearGradient id="portraitTone" x1="0" y1="0" x2="0" y2="1">
        <stop offset="0" stop-color="#5a2c1c"/>
        <stop offset="0.4" stop-color="#b57d52"/>
        <stop offset="0.75" stop-color="#e3b48f"/>
        <stop offset="1" stop-color="#8fd6d8"/>
      </linearGradient>
    </defs>
    <path d="M430,45 C450,110 530,190 530,275 A105,105 0 1 1 320,275 C320,190 410,110 430,45 Z" fill="url(#portraitTone)"/>
  </svg>

  <ul class="service-list">
    <li class="service-item">
      <svg viewBox="0 0 28 28" fill="none" stroke="#fff" stroke-width="1.4"><path d="M4,13 L14,5 L24,13"/><path d="M7,11 V24 H21 V11"/><rect x="10" y="17" width="4" height="7"/><rect x="16" y="16" width="4" height="4"/></svg>
      Grout and Silicone Repair
    </li>
    <li class="service-item">
      <svg viewBox="0 0 28 28" fill="none" stroke="#fff" stroke-width="1.4"><rect x="3" y="9" width="22" height="16"/><path d="M3,14 H25 M3,19 H25 M9,9 V14 M17,9 V14 M13,14 V19 M21,14 V19 M9,19 V25 M17,19 V25"/><path d="M18,8 L24,2"/></svg>
      Broken or Drummy Tile Replacement
    </li>
    <li class="service-item">
      <svg viewBox="0 0 28 28" fill="none" stroke="#fff" stroke-width="1.4"><rect x="4" y="3" width="18" height="6" rx="1"/><path d="M22,6 H25 V12 H13 V16"/><rect x="11" y="16" width="4" height="9"/></svg>
      Grout Sealing
    </li>
  </ul>

  <div class="cta">
    <div class="cta-title">CALL US TODAY!</div>
    <div class="cta-phone">0417 386 240</div>
  </div>
  <div class="contact-pill contact-pill--email">
    <svg viewBox="0 0 17 17"><circle cx="8.5" cy="8.5" r="8.5" fill="#fff"/><rect x="4" y="5.5" width="9" height="6" rx="1" fill="none" stroke="#2b9fd9" stroke-width="1.2"/><path d="M4,6 L8.5,9 L13,6" fill="none" stroke="#2b9fd9" stroke-width="1.2"/></svg>
    hello@kestrelbayfinishes.com.au
  </div>
  <div class="contact-pill contact-pill--web">
    <svg viewBox="0 0 17 17"><circle cx="8.5" cy="8.5" r="8.5" fill="#fff"/><circle cx="8.5" cy="8.5" r="4.8" fill="none" stroke="#2b9fd9" stroke-width="1.1"/><path d="M3.7,8.5 H13.3 M8.5,3.7 V13.3" stroke="#2b9fd9" stroke-width="1.1"/></svg>
    www.kestrelbayfinishes.com.au
  </div>
</section>

<!-- Post 2: We love to make your tiles smile -->
<section class="post post--smile">
  <div class="photo-backdrop" role="img" aria-label="Bright white marble bathroom with bathtub and sea view window"></div>

  <div class="brand-mark" style="left:147px"></div>
  <div class="brand-name" style="left:77px">KESTREL BAY FINISHES</div>

  <div class="values">WE BELIEVE<br>WE LISTEN<br>WE COMMIT</div>

  <div class="tagline">WE LOVE TO MAKE<br><span class="accent">YOUR TILES SMILE!</span></div>
  <svg class="smile-swoosh" width="513" height="513" viewBox="0 0 513 513" aria-hidden="true">
    <path d="M27,254 C110,290 230,288 305,252" fill="none" stroke="#2b9fd9" stroke-width="4" stroke-linecap="round"/>
  </svg>

  <div class="service-band"></div>

  <div class="photo-slot--smile" role="img" aria-label="Photo of a smiling young woman with hands at her cheeks"></div>

  <ul class="service-list">
    <li class="service-item">
      <svg viewBox="0 0 28 28" fill="none" stroke="#fff" stroke-width="1.4"><path d="M4,13 L14,5 L24,13"/><path d="M7,11 V24 H21 V11"/><rect x="10" y="17" width="4" height="7"/><rect x="16" y="16" width="4" height="4"/></svg>
      Grout and Silicone Repair
    </li>
    <li class="service-item">
      <svg viewBox="0 0 28 28" fill="none" stroke="#fff" stroke-width="1.4"><rect x="3" y="9" width="22" height="16"/><path d="M3,14 H25 M3,19 H25 M9,9 V14 M17,9 V14 M13,14 V19 M21,14 V19 M9,19 V25 M17,19 V25"/><path d="M18,8 L24,2"/></svg>
      Broken or Drummy Tile Replacement
    </li>
    <li class="service-item">
      <svg viewBox="0 0 28 28" fill="none" stroke="#fff" stroke-width="1.4"><rect x="4" y="3" width="18" height="6" rx="1"/><path d="M22,6 H25 V12 H13 V16"/><rect x="11" y="16" width="4" height="9"/></svg>
      Grout Sealing
    </li>
  </ul>

  <div class="cta">
    <div class="cta-title">CALL US TODAY!</div>
    <div class="cta-phone">0417 386 240</div>
  </div>
  <div class="contact-pill contact-pill--email">
    <svg viewBox="0 0 17 17"><circle cx="8.5" cy="8.5" r="8.5" fill="#fff"/><rect x="4" y="5.5" width="9" height="6" rx="1" fill="none" stroke="#2b9fd9" stroke-width="1.2"/><path d="M4,6 L8.5,9 L13,6" fill="none" stroke="#2b9fd9" stroke-width="1.2"/></svg>
    hello@kestrelbayfinishes.com.au
  </div>
  <div class="contact-pill contact-pill--web">
    <svg viewBox="0 0 17 17"><circle cx="8.5" cy="8.5" r="8.5" fill="#fff"/><circle cx="8.5" cy="8.5" r="4.8" fill="none" stroke="#2b9fd9" stroke-width="1.1"/><path d="M3.7,8.5 H13.3 M8.5,3.7 V13.3" stroke="#2b9fd9" stroke-width="1.1"/></svg>
    www.kestrelbayfinishes.com.au
  </div>
</section>

<div class="size-label" style="left:70px">1080X1080</div>
<div class="size-label" style="left:617px">1080X1080</div>

<div class="progress-note">*WORK IN PROOGRESS<br>for 3 more template</div>

</body>
</html>
```